Telecommunications/Power civil contractor needs business card design

Were a new telecommunications/power underground civil contractor that is looking for a new business card design. Our company colours are silver or grey and orange. Feel free to use the white background logo or the black background logo.

Target Market(s)

Local contractors, utility companies, private sector mining/energy companies, developers.

Industry/Entity Type

Telecommunications

Contact Information for Business Card

Each card will need the following info:
Persons name:
Title:
E-mail:
Phone number:
Shop Address:
Mailing Address:

Requirements
Must have
• Each card will need the following info:
• Persons name:
• Title:
• E-mail:
• Phone number:
• Shop Address:
• Mailing Address:

```html
<!DOCTYPE html>
<html lang="en">
<head>
<meta charset="utf-8">
<title>Ternline Contracting Inc – Business Card</title>
<link href="https://fonts.googleapis.com/css2?family=Open+Sans:wght@400;700&display=swap" rel="stylesheet">
<style>
  :root {
    --orange: #f15a24;
    --grey: #8a8a8a;
    --grey-dark: #5a5a5a;
    --white: #ffffff;
    --black: #141414;
    --backdrop: #e6e6e6;
  }
  * { margin: 0; padding: 0; box-sizing: border-box; }
  html, body { width: 1200px; height: 907px; overflow: hidden; }
  body {
    background: var(--backdrop);
    font-family: "Open Sans", Arial, sans-serif;
    display: flex;
    align-items: center;
    justify-content: center;
    gap: 40px;
  }
  .card {
    position: relative;
    width: 540px;
    height: 309px;
    overflow: hidden;
    box-shadow: 0 6px 18px rgba(0,0,0,0.18);
  }
  .card-front { background: var(--white); }
  .front-shape { position: absolute; inset: 0; }
  .contact {
    position: absolute;
    left: 30px;
    top: 92px;
    color: var(--white);
    font-size: 13px;
    line-height: 1.4;
    white-space: nowrap;
  }
  .contact .person-name { font-weight: 700; font-size: 16px; }
  .contact .person-title { color: var(--grey-dark); font-size: 15px; margin-bottom: 10px; }
  .contact-line { display: flex; align-items: center; gap: 7px; }
  .contact-icon { width: 14px; height: 14px; flex: none; }
  .address { margin-top: 12px; }
  .brand {
    position: absolute;
    display: flex;
    flex-direction: column;
    align-items: center;
    gap: 10px;
    text-align: center;
  }
  .brand-dot {
    border-radius: 50%;
    border: 3px solid var(--orange);
    flex: none;
  }
  .brand-name {
    color: var(--orange);
    font-weight: 700;
    line-height: 1.1;
    text-transform: uppercase;
    white-space: nowrap;
  }
  .card-front .brand { right: 36px; top: 62px; }
  .card-front .brand-dot { width: 48px; height: 48px; }
  .card-front .brand-name { font-size: 18px; }
  .card-back { background: var(--black); }
  .card-back .brand {
    left: 50%; top: 50%;
    transform: translate(-50%, -50%);
    gap: 14px;
  }
  .card-back .brand-dot { width: 70px; height: 70px; }
  .card-back .brand-name { font-size: 26px; }
</style>
</head>
<body>
  <section class="card card-front">
    <svg class="front-shape" viewBox="0 0 540 309" width="540" height="309" aria-hidden="true">
      <path d="M0 0 H340 C280 30 292 120 282 180 C270 250 200 285 0 298 Z" fill="var(--orange)"/>
      <path d="M282 180 C270 250 200 285 0 298 L0 312 C212 302 286 262 292 188 Z" fill="var(--grey)"/>
      <path d="M352 0 C312 22 302 70 302 125 C298 70 304 24 338 0 Z" fill="var(--grey)" opacity="0.7"/>
    </svg>
    <div class="contact">
      <div class="person-name">Dale Marsh</div>
      <div class="person-title">Managing Director</div>
      <div class="contact-line">
        <svg class="contact-icon" viewBox="0 0 14 14"><circle cx="7" cy="7" r="7" fill="var(--grey-dark)"/><path d="M4.5 3.5 L6 5 L5.3 6 C5.8 7 6.9 8.2 8 8.7 L9 8 L10.5 9.5 L9.6 10.5 C7 10.3 3.8 7 3.5 4.4 Z" fill="var(--white)"/></svg>
        <span>555.014.207</span>
      </div>
      <div class="contact-line">
        <svg class="contact-icon" viewBox="0 0 14 14"><circle cx="7" cy="7" r="7" fill="var(--grey-dark)"/><rect x="3.5" y="4.5" width="7" height="5" fill="none" stroke="var(--white)" stroke-width="1"/><path d="M3.5 4.5 L7 7.3 L10.5 4.5" fill="none" stroke="var(--white)" stroke-width="1"/></svg>
        <span>info@ternlinecontracting.com</span>
      </div>
      <div class="address">No. 4 Ridge Road,<br>Suite 210, Alder Falls,<br>WA 55501</div>
    </div>
    <div class="brand">
      <span class="brand-dot"></span>
      <span class="brand-name">Ternline<br>Contracting Inc</span>
    </div>
  </section>

  <section class="card card-back">
    <div class="brand">
      <span class="brand-dot"></span>
      <span class="brand-name">Ternline<br>Contracting Inc</span>
    </div>
  </section>
</body>
</html>
```